Harrowmere Freight, Project

Company Profile
Harrowmere Freight Sdn Bhd is a well established and experienced freight forwarder in Kuala Lumpur, Malaysia. We specialize in air and sea forwarding, Custom Brokerage and regulatory compliance services, inland transportation,
overseas freighting and warehousing and distribution management. With our dedicated qualified and experienced professionals, we are fully committed to serving our clients.

Our Mission
Based on the motto “Quick, Reliable and Polite”, Harrowmere Freight is dedicated to upholding the following three points corporate philosophy:
1. Adhering to the principle that “the customer always comes first”.
2. Contributing to the development of the local community.
3. Making it our duty to be responsible and sincere.

Our Edge
• One-Stop Logistics Solutions
• Extensive Network Throughout Malaysia
• Highly Qualified and Experienced Pool of Professionals
• Comprehensive IT Solutions
• Innovative and Customer-focused Solutions
• Flexible and Consistent in Managing Exceptions
• Total Supply Chain Visibility

Target Market(s)

We sell the logistics services to all the industry in Malaysia. (ONE Stop Logistics Solutions)

Industry/Entity Type

Logistic

Contact Information for Business Card

I want the back of the card to be white with the logo and slogan. i would like to see the logo on the front with the general info.

Requirements
Must have
• Name, Title, Office, Cell, Fax, Email, Address, Website
Nice to have
• Modern Design Business Card

```html
<!DOCTYPE html>
<html lang="en">
<head>
<meta charset="utf-8">
<title>Harrowmere Freight – Business Card</title>
<link rel="stylesheet" href="https://fonts.googleapis.com/css2?family=Open+Sans:wght@400;600;700&display=swap">
<style>
  :root {
    --blue-light: #4cc6e8;
    --blue: #2ba3dc;
    --blue-deep: #1b7fc8;
    --grey: #6e7175;
    --grey-dark: #4a4d51;
    --ink: #3b3e42;
    --paper: #ffffff;
    --stage: #e8e3da;
  }
  * { box-sizing: border-box; margin: 0; padding: 0; }
  html, body { width: 1200px; height: 1200px; overflow: hidden; }
  body {
    font-family: "Open Sans", sans-serif;
    background: var(--stage);
    position: relative;
  }
  .brand-header {
    position: absolute; left: 0; top: 0;
    width: 1200px; height: 220px;
    background: var(--paper);
    display: flex; flex-direction: column; align-items: center; justify-content: center;
  }
  .brand-mark { display: flex; align-items: center; gap: 12px; }
  .brand-mark .dot { width: 18px; height: 18px; border-radius: 50%; background: var(--blue); }
  .brand-mark .name { font-size: 34px; font-weight: 600; color: var(--grey-dark); letter-spacing: 0.5px; }

  .card {
    position: absolute; left: 260px;
    width: 680px; height: 389px;
    border-radius: 6px; overflow: hidden;
    box-shadow: 0 6px 0 var(--blue-deep), 0 14px 28px rgba(0,0,0,0.18);
  }
  .card svg.card-bg { position: absolute; inset: 0; }

  /* Services card */
  .card--services { top: 262px; }
  .services-tagline {
    position: absolute; left: 0; top: 22px; width: 100%;
    text-align: center; color: #fff; font-size: 17px; font-weight: 600; letter-spacing: 0.5px;
  }
  .services-body {
    position: absolute; left: 40px; right: 40px; top: 118px;
    text-align: center; color: #fff;
  }
  .services-heading { font-size: 22px; letter-spacing: 0.5px; }
  .services-rule { width: 110px; height: 1px; background: rgba(255,255,255,0.85); margin: 16px auto 18px; }
  .services-list { font-size: 16.5px; line-height: 1.55; }

  /* Contact card */
  .card--contact { top: 691px; }
  .contact-brand {
    position: absolute; right: 60px; top: 62px;
    display: flex; align-items: center; gap: 10px;
  }
  .contact-brand .dot { width: 14px; height: 14px; border-radius: 50%; background: var(--blue); }
  .contact-brand .name { font-size: 27px; font-weight: 600; color: var(--grey-dark); }
  .person { position: absolute; left: 40px; top: 64px; color: var(--ink); }
  .person-name { font-size: 22px; font-weight: 600; letter-spacing: 0.5px; }
  .person-title { font-size: 16px; color: var(--grey); margin-top: 2px; }
  .contact-list { list-style: none; position: absolute; left: 40px; top: 140px; font-size: 14px; color: var(--ink); }
  .contact-list li { display: flex; align-items: center; gap: 10px; height: 23px; }
  .contact-list li.gap { margin-top: 10px; }
  .contact-list svg { width: 16px; height: 16px; flex: none; }
  .contact-list .hl { color: var(--blue); }
  .company-line {
    position: absolute; right: 34px; bottom: 50px;
    color: #fff; font-size: 15px; font-weight: 700; text-align: right; white-space: nowrap;
  }
  .company-address {
    position: absolute; right: 34px; bottom: 26px;
    color: #fff; font-size: 10.5px; text-align: right; white-space: nowrap;
  }
</style>
</head>
<body>

<header class="brand-header">
  <div class="brand-mark">
    <span class="dot"></span>
    <span class="name">Harrowmere Freight</span>
  </div>
</header>

<section class="card card--services">
  <svg class="card-bg" width="680" height="389" viewBox="0 0 680 389" aria-hidden="true">
    <defs>
      <linearGradient id="svcBlue" x1="0" y1="0" x2="1" y2="1">
        <stop offset="0" stop-color="#4cc6e8"/>
        <stop offset="1" stop-color="#1e8fd2"/>
      </linearGradient>
    </defs>
    <rect width="680" height="389" fill="url(#svcBlue)"/>
    <path d="M0 0 H680 V48 Q340 78 0 64 Z" fill="#6e7175"/>
  </svg>
  <div class="services-tagline">ONE STOP LOGISTICS SOLUTIONS</div>
  <div class="services-body">
    <div class="services-heading">WE'RE SPECIALIZE IN</div>
    <div class="services-rule"></div>
    <p class="services-list">
      • International Shipping (Air / Sea) • Transportation / Haulage<br>
      • Consolidation – NVOCC • Project Management<br>
      • Packing • Supply Chain Management • Warehousing<br>
      • Marine Insurance • Tax Exemption Consultancy • Distribution<br>
      • Custom Brokerage • Door to Door
    </p>
  </div>
</section>

<section class="card card--contact">
  <svg class="card-bg" width="680" height="389" viewBox="0 0 680 389" aria-hidden="true">
    <defs>
      <linearGradient id="ctBlue" x1="0" y1="0" x2="1" y2="0">
        <stop offset="0" stop-color="#4cc6e8"/>
        <stop offset="1" stop-color="#1e8fd2"/>
      </linearGradient>
    </defs>
    <rect width="680" height="389" fill="#ffffff"/>
    <path d="M0 389 V332 Q360 300 680 200 V389 Z" fill="url(#ctBlue)"/>
  </svg>
  <div class="contact-brand">
    <span class="dot"></span>
    <span class="name">Harrowmere Freight</span>
  </div>
  <div class="person">
    <div class="person-name">DANIAL ROSLAN</div>
    <div class="person-title">Managing Director</div>
  </div>
  <ul class="contact-list">
    <li>
      <svg viewBox="0 0 16 16"><rect width="16" height="16" rx="2" fill="#2ba3dc"/><rect x="5" y="3" width="6" height="10" rx="1" fill="none" stroke="#fff" stroke-width="1.3"/></svg>
      + 6012-480 2715
    </li>
    <li>
      <svg viewBox="0 0 16 16"><rect width="16" height="16" rx="2" fill="#2ba3dc"/><path d="M4 4 Q4 12 12 12 L12 10 L10 9 L9 10 Q6 9 6 7 L7 6 L6 4 Z" fill="#fff"/></svg>
      + (603) 3347 2180 / 2181
    </li>
    <li>
      <svg viewBox="0 0 16 16"><rect width="16" height="16" rx="2" fill="#2ba3dc"/><rect x="3" y="6" width="10" height="6" fill="none" stroke="#fff" stroke-width="1.3"/><rect x="5" y="3" width="6" height="3" fill="#fff"/></svg>
      + (603) 3347 2190
    </li>
    <li class="gap">
      <svg viewBox="0 0 16 16"><rect width="16" height="16" rx="2" fill="#2ba3dc"/><rect x="3" y="4.5" width="10" height="7" fill="none" stroke="#fff" stroke-width="1.2"/><path d="M3 4.5 L8 9 L13 4.5" fill="none" stroke="#fff" stroke-width="1.2"/></svg>
      <span>danial.roslan@<span class="hl">harrowmere</span>.com.my</span>
    </li>
    <li>
      <svg viewBox="0 0 16 16"><rect width="16" height="16" rx="2" fill="#2ba3dc"/><circle cx="8" cy="8" r="5" fill="none" stroke="#fff" stroke-width="1.2"/><path d="M3 8 H13 M8 3 Q5 8 8 13 M8 3 Q11 8 8 13" fill="none" stroke="#fff" stroke-width="1"/></svg>
      <span>www.<span class="hl">harrowmere</span>.com.my</span>
    </li>
  </ul>
  <div class="company-line">HARROWMERE FREIGHT SDN. BHD. (1184276-K)</div>
  <div class="company-address">No. 14B, 2nd Floor, Jalan Seri Anggerik 3, Taman Anggerik, 41300 Klang, Selangor Darul Ehsan, Malaysia</div>
</section>

</body>
</html>
```